Veltrano.co - Polar Expeditions Specialists

We need a modern, visually striking business card for Veltrano.co, a company specialized in selling expedition cruises to the most remote regions on Earth, with a focus on the Arctic and Antarctica. The design should instantly communicate that the cardholder is an expert in polar travel. Use clean, premium aesthetics with cool tones like icy blue and white, possibly incorporating polar imagery (ice, glaciers, penguins, etc.)

Attached the logo

Contact Information for Business Card

Feels high-end and trustworthy.. Visually memorable — encourages people to keep it

Colors
0054AA
0677BA
7BADD7
CADEEF
E8F1F8

Requirements
Must have
• ice, glaciers, penguins, montains
Nice to have
• modern, transparente,

```html
<!DOCTYPE html>
<html lang="en">
<head>
<meta charset="utf-8">
<title>Veltrano.co – Business Card</title>
<link rel="stylesheet" href="https://fonts.googleapis.com/css2?family=Poppins:wght@600;700&family=Lato:wght@400;700&display=swap">
<style>
  :root {
    --stage: #2a2a2b;
    --card-blue: #3676b8;
    --brand-blue: #3372b6;
    --white: #ffffff;
    --ink: #1b1b1b;
    --rule: #1f1f1f;
  }
  html, body {
    margin: 0;
    padding: 0;
    width: 1200px;
    height: 694px;
    overflow: hidden;
    background: var(--stage);
  }
  .canvas {
    position: relative;
    width: 1200px;
    height: 694px;
  }
  .card {
    position: absolute;
    top: 192px;
    width: 540px;
    height: 309px;
    border-radius: 22px;
    box-shadow: 0 18px 40px rgba(0,0,0,.45);
    overflow: hidden;
  }
  .card--front { left: 40px; background: var(--card-blue); }
  .card--back  { left: 620px; background: var(--white); }

  .brand {
    font-family: "Poppins", sans-serif;
    font-weight: 700;
    display: flex;
    flex-direction: column;
    align-items: center;
  }
  .brand__row { display: flex; align-items: center; gap: 12px; }
  .brand__dot { border-radius: 50%; flex: none; }
  .brand__name { line-height: 1; letter-spacing: .5px; white-space: nowrap; }
  .brand__tagline { font-weight: 600; line-height: 1; white-space: nowrap; }

  .card--front .brand {
    position: absolute;
    left: 0; right: 0; top: 106px;
    color: var(--white);
  }
  .card--front .brand__dot { width: 26px; height: 26px; background: var(--white); }
  .card--front .brand__name { font-size: 56px; }
  .card--front .brand__tagline { font-size: 16px; margin-top: 12px; }

  .card--back .brand {
    position: absolute;
    right: 30px; top: 40px;
    color: var(--brand-blue);
    align-items: flex-end;
  }
  .card--back .brand__dot { width: 18px; height: 18px; background: var(--brand-blue); }
  .card--back .brand__name { font-size: 40px; }
  .card--back .brand__tagline { font-size: 12px; margin-top: 8px; }

  .holder {
    position: absolute;
    left: 40px; top: 134px;
    font-family: "Lato", sans-serif;
  }
  .holder__name {
    font-weight: 700;
    font-size: 25px;
    line-height: 1.1;
    color: var(--brand-blue);
    margin: 0;
  }
  .holder__role {
    font-size: 17px;
    line-height: 1.2;
    color: var(--ink);
    margin: 4px 0 0;
  }
  .divider {
    position: absolute;
    left: 40px; right: 30px; top: 194px;
    height: 1px;
    background: var(--rule);
  }
  .contacts {
    position: absolute;
    left: 40px; top: 208px;
    list-style: none; margin: 0; padding: 0;
    font-family: "Lato", sans-serif;
    font-size: 15px;
    color: var(--ink);
  }
  .contacts li { display: flex; align-items: center; gap: 10px; height: 24px; }
  .contacts svg { width: 15px; height: 15px; fill: var(--brand-blue); flex: none; }
  .address {
    position: absolute;
    right: 30px; top: 212px;
    margin: 0;
    font-family: "Lato", sans-serif;
    font-style: normal;
    font-size: 15px;
    line-height: 24px;
    color: var(--ink);
    text-align: right;
  }
</style>
</head>
<body>
<main class="canvas">
  <section class="card card--front" aria-label="Card front">
    <div class="brand">
      <div class="brand__row">
        <span class="brand__dot"></span>
        <span class="brand__name">Veltrano.co</span>
      </div>
      <span class="brand__tagline">Polar Expeditions Specialists</span>
    </div>
  </section>

  <section class="card card--back" aria-label="Card back">
    <div class="brand">
      <div class="brand__row">
        <span class="brand__dot"></span>
        <span class="brand__name">Veltrano.co</span>
      </div>
      <span class="brand__tagline">Polar Expeditions Specialists</span>
    </div>

    <div class="holder">
      <p class="holder__name">Marcus Hale</p>
      <p class="holder__role">Owner</p>
    </div>

    <div class="divider"></div>

    <ul class="contacts">
      <li>
        <svg viewBox="0 0 24 24" aria-hidden="true"><path d="M6.6 10.8a15.1 15.1 0 0 0 6.6 6.6l2.2-2.2c.3-.3.7-.4 1-.2 1.1.4 2.3.6 3.6.6.6 0 1 .4 1 1V20c0 .6-.4 1-1 1A17 17 0 0 1 3 4c0-.6.4-1 1-1h3.5c.6 0 1 .4 1 1 0 1.3.2 2.5.6 3.6.1.3 0 .7-.2 1z"/></svg>
        <span>055-870 312 446</span>
      </li>
      <li>
        <svg viewBox="0 0 24 24" aria-hidden="true"><path d="M2 5h20v14H2z"/><path d="M3 6l9 7 9-7v1.4l-9 7-9-7z" fill="#fff"/></svg>
        <span>hello@veltrano.co</span>
      </li>
      <li>
        <svg viewBox="0 0 24 24" aria-hidden="true"><circle cx="12" cy="12" r="10"/><path d="M2 12h20M12 2c3 3 3 17 0 20M12 2c-3 3-3 17 0 20" stroke="#fff" stroke-width="1.4" fill="none"/></svg>
        <span>www.veltrano.co</span>
      </li>
    </ul>

    <address class="address">18, Harbour Quay Road<br>90210, Norlandia</address>
  </section>
</main>
</body>
</html>
```